Veldmark Supplies Business Card

Professional business card that stand out to our potential customers. Front and back with clean modern design

Industry/Entity Type

Oil and gas

Contact Information for Business Card

Name, address, website , office phone and cell number

Requirements
Must have
• Editable files for each employee

```html
<!DOCTYPE html>
<html lang="en">
<head>
<meta charset="utf-8">
<title>Veldmark Supplies Business Card</title>
<link rel="stylesheet" href="https://fonts.googleapis.com/css2?family=Montserrat:wght@500;600;800&display=swap">
<style>
  :root {
    --stage: #222222;
    --brand-blue: #05afd4;
    --brand-red: #f5141c;
    --paper: #ffffff;
  }
  * { box-sizing: border-box; margin: 0; padding: 0; }
  html, body { width: 1200px; height: 711px; overflow: hidden; background: var(--stage); }
  body { display: flex; align-items: center; justify-content: center; gap: 70px; font-family: "Montserrat", sans-serif; }

  .card {
    position: relative;
    width: 340px;
    height: 580px;
    border-radius: 26px;
    overflow: hidden;
    background: var(--brand-blue);
    color: var(--paper);
  }

  /* Back */
  .card-back { display: flex; align-items: center; justify-content: center; }
  .back-mark { display: flex; align-items: center; gap: 14px; }
  .back-mark .mark-square { width: 34px; height: 34px; background: var(--paper); }
  .back-mark .mark-name { font-weight: 800; font-size: 22px; letter-spacing: 1.5px; text-transform: uppercase; color: var(--paper); }

  /* Front */
  .front-top { position: absolute; inset: 0; }
  .front-header { position: absolute; top: 34px; left: 0; right: 0; display: flex; align-items: center; justify-content: center; gap: 10px; }
  .front-header .mark-square { width: 22px; height: 22px; background: var(--brand-red); }
  .front-header .mark-name { font-weight: 800; font-size: 19px; letter-spacing: 1.5px; text-transform: uppercase; color: var(--brand-red); }

  .front-body { position: absolute; top: 262px; left: 0; right: 0; text-align: center; }
  .person { display: flex; align-items: center; justify-content: center; gap: 10px; }
  .person-rule { width: 52px; height: 2px; background: var(--paper); }
  .person-name { font-weight: 800; font-size: 25px; letter-spacing: .5px; text-transform: uppercase; }
  .person-title { font-weight: 500; font-size: 14px; letter-spacing: 1px; margin-top: 2px; }

  .icon-row { display: flex; justify-content: center; gap: 14px; margin-top: 22px; }
  .icon { width: 30px; height: 30px; background: var(--brand-red); display: flex; align-items: center; justify-content: center; }
  .icon svg { width: 18px; height: 18px; }

  .contact-list { list-style: none; margin-top: 16px; font-weight: 500; font-size: 14.5px; line-height: 1.45; }
  .divider { width: 250px; height: 1px; background: var(--paper); margin: 14px auto 10px; }
  .address { font-style: normal; font-weight: 500; font-size: 14.5px; line-height: 1.45; }
</style>
</head>
<body>

  <section class="card card-back" aria-label="Card back">
    <div class="back-mark">
      <span class="mark-square"></span>
      <span class="mark-name">Veldmark Supplies</span>
    </div>
  </section>

  <section class="card card-front" aria-label="Card front">
    <svg class="front-top" viewBox="0 0 340 580" preserveAspectRatio="none" aria-hidden="true">
      <polygon points="0,0 340,0 340,70 0,230" fill="#ffffff"/>
    </svg>

    <header class="front-header">
      <span class="mark-square"></span>
      <span class="mark-name">Veldmark Supplies</span>
    </header>

    <div class="front-body">
      <div class="person">
        <span class="person-rule"></span>
        <h1 class="person-name">Dara Kellworth</h1>
        <span class="person-rule"></span>
      </div>
      <p class="person-title">President</p>

      <div class="icon-row">
        <span class="icon" aria-label="Office phone">
          <svg viewBox="0 0 24 24"><path fill="#fff" d="M3 9c0-3 4-5 9-5s9 2 9 5v2h-5V9H8v2H3z M6 12h12l2 8H4z"/></svg>
        </span>
        <span class="icon" aria-label="Mobile">
          <svg viewBox="0 0 24 24"><rect x="7" y="2" width="10" height="20" rx="2" fill="none" stroke="#fff" stroke-width="2"/><circle cx="12" cy="18" r="1.2" fill="#fff"/></svg>
        </span>
        <span class="icon" aria-label="Email">
          <svg viewBox="0 0 24 24"><rect x="2" y="5" width="20" height="14" fill="none" stroke="#fff" stroke-width="2"/><path d="M2 5l10 8 10-8" fill="none" stroke="#fff" stroke-width="2"/></svg>
        </span>
        <span class="icon" aria-label="Website">
          <svg viewBox="0 0 24 24"><circle cx="12" cy="12" r="9" fill="none" stroke="#fff" stroke-width="2"/><path d="M3 12h18M12 3c4 4 4 14 0 18M12 3c-4 4-4 14 0 18" fill="none" stroke="#fff" stroke-width="1.6"/></svg>
        </span>
      </div>

      <ul class="contact-list">
        <li>555-210-4417</li>
        <li>000-000-9999</li>
        <li>info@example-youremail.com</li>
        <li>www.example-yourwebsite.com</li>
      </ul>

      <div class="divider"></div>

      <address class="address">482 Harlow Ave, Ste<br>100, Brenton, TX 75201</address>
    </div>
  </section>

</body>
</html>
```